Business Card- Can you make it cool vs boring!

Need a refresh on my business card! Want it to be modern but simple, classic and a pop of coolness! we do senior living and it is boring. but that doesn't mean our business card have to look boring! Open to two sided cards. our website is www.Dunmere-PK.com

Target Market(s)

capital market

Industry/Entity Type

senior housing/ real estate

Contact Information for Business Card

logo/ name/ cell/ address/ www.Dunmere-PK.com/ space for a QR code

Requirements
Must have
• maybe a QR code (do not make prominent I may not use the QR so design where it can be taken out) that link to more about us/ landing page. needs to be modern but clean
Should not have
• clip art or script

```html
<!DOCTYPE html>
<html lang="en">
<head>
<meta charset="utf-8">
<title>Dunmere Living – Business Card</title>
<link href="https://fonts.googleapis.com/css2?family=Arimo:wght@400;700&display=swap" rel="stylesheet">
<style>
  :root {
    --backdrop: #dcdcdc;
    --rust: #b4582e;
    --rust-light: #ba6439;
    --rust-dark: #ad5027;
    --paper: #ffffff;
    --edge-grey: #8e8f93;
    --gold: #e4b25a;
  }
  * { margin: 0; padding: 0; box-sizing: border-box; }
  html, body { width: 1200px; height: 1200px; overflow: hidden; }
  body {
    background: var(--backdrop);
    font-family: "Arimo", Arial, sans-serif;
    position: relative;
  }
  .card {
    position: absolute;
    width: 688px;
    height: 393px;
    overflow: hidden;
  }
  .card--front { left: 267px; top: 159px; background: var(--paper); }
  .card--back {
    left: 262px; top: 653px;
    background: linear-gradient(180deg, var(--rust-light), var(--rust-dark));
  }
  .front-shape { position: absolute; inset: 0; }
  .brand-front {
    position: absolute;
    left: 0; width: 360px;
    top: 170px;
    text-align: center;
    color: var(--rust);
    font-size: 36px;
    font-weight: 400;
    letter-spacing: 1px;
  }
  .contact {
    position: absolute;
    left: 413px;
    top: 80px;
    color: #fff;
  }
  .contact__name { font-size: 24px; font-weight: 700; letter-spacing: 0.3px; }
  .contact__role { font-size: 15.5px; margin-top: 3px; }
  .contact__address { font-size: 16px; line-height: 20.5px; margin-top: 19px; }
  .contact__lines { list-style: none; margin-top: 15px; font-size: 16px; }
  .contact__lines li {
    display: flex; align-items: center; gap: 10px; height: 20.5px;
  }
  .contact__lines svg { width: 14px; height: 14px; margin-left: -2px; flex: none; }
  .brand-back {
    position: absolute;
    inset: 0;
    display: flex; align-items: center; justify-content: center;
    color: var(--gold);
    font-size: 56px;
    font-weight: 400;
    letter-spacing: 2px;
  }
</style>
</head>
<body>

<section class="card card--front">
  <svg class="front-shape" viewBox="0 0 688 393" width="688" height="393" aria-hidden="true">
    <path d="M312,0 Q410,196 306,393 L316,393 Q418,196 320,0 Z" fill="var(--edge-grey)"/>
    <path d="M320,0 Q418,196 316,393 L688,393 L688,0 Z" fill="var(--rust)"/>
    <rect x="320" y="0" width="368" height="6" fill="var(--rust-dark)"/>
  </svg>

  <div class="brand-front">Dunmere Living</div>

  <div class="contact">
    <div class="contact__name">DANIEL CARTER</div>
    <div class="contact__role">President</div>
    <div class="contact__address">
      4870 Cedar Hollow Road<br>
      Suite #1420<br>
      Maple Springs, TX<br>
      United States, Texas
    </div>
    <ul class="contact__lines">
      <li>
        <svg viewBox="0 0 24 24" aria-hidden="true"><path fill="#fff" d="M6.6 10.8a15.2 15.2 0 0 0 6.6 6.6l2.2-2.2c.3-.3.7-.4 1-.2 1.1.4 2.3.6 3.6.6.6 0 1 .4 1 1V20c0 .6-.4 1-1 1C10.6 21 3 13.4 3 4c0-.6.4-1 1-1h3.5c.6 0 1 .4 1 1 0 1.3.2 2.5.6 3.6.1.3 0 .7-.2 1z"/></svg>
        281-555-0147
      </li>
      <li>
        <svg viewBox="0 0 24 24" aria-hidden="true"><rect x="2" y="5" width="20" height="14" fill="#fff"/><path d="M2 5l10 8 10-8" fill="none" stroke="var(--rust)" stroke-width="2"/></svg>
        info@Dunmere-PK.com
      </li>
      <li>
        <svg viewBox="0 0 24 24" aria-hidden="true"><circle cx="12" cy="12" r="10" fill="#fff"/><path d="M7 7c2 1 3 3 2 5s1 3 2 5M15 5c-1 2 1 3 3 3M14 19c0-2 2-3 4-3" fill="none" stroke="var(--rust)" stroke-width="2"/></svg>
        www.Dunmere-PK.com
      </li>
    </ul>
  </div>
</section>

<section class="card card--back">
  <div class="brand-back">Dunmere Living</div>
</section>

</body>
</html>
```